Brellwick Partners, LLC Stationary

Brellwick Partners, LLC is a new financial planning and consulting company. We are looking for designs on business cards, letterhead, envelopes, and anything else that would be useful. Our preference for business card design is two sided. We are looking for a professional and clean look with incorporating the logo and patriotic feel. Thank you to all who participate and good luck!

```html
<!DOCTYPE html>
<html lang="en">
<head>
<meta charset="utf-8">
<title>Brellwick Partners, LLC — Stationery</title>
<link rel="stylesheet" href="https://fonts.googleapis.com/css2?family=Questrial&display=swap">
<style>
  :root {
    --navy: #1f3a6b;
    --red: #c0272d;
    --paper: #ffffff;
    --backdrop: #666666;
    --rule: #dcdcdc;
    --mark-faint: #efefef;
  }
  * { box-sizing: border-box; margin: 0; padding: 0; }
  html, body { width: 720px; height: 1200px; overflow: hidden; }
  body {
    background: var(--backdrop);
    font-family: "Questrial", "Century Gothic", sans-serif;
    position: relative;
  }
  .sheet {
    position: absolute;
    background: var(--paper);
    overflow: hidden;
  }
  .letterhead { left: 80px; top: 56px; width: 560px; height: 758px; }
  .business-card { left: 80px; top: 835px; width: 564px; height: 335px; }

  .brand {
    display: flex;
    align-items: center;
    gap: 8px;
    color: var(--navy);
    text-transform: uppercase;
    letter-spacing: 0.5px;
  }
  .brand-square { background: var(--red); flex: none; }
  .letterhead .brand { position: absolute; left: 46px; top: 62px; font-size: 17px; }
  .letterhead .brand-square { width: 14px; height: 14px; }
  .business-card .brand {
    position: absolute; left: 0; right: 0; top: 62px;
    justify-content: center; font-size: 26px;
  }
  .business-card .brand-square { width: 20px; height: 20px; }

  .backdrop-mark {
    position: absolute; left: 170px; top: 360px;
    width: 360px; height: 360px; border-radius: 50%;
    background: var(--mark-faint);
  }

  .letterhead-footer {
    position: absolute; left: 0; right: 0; top: 728px;
    text-align: center; font-size: 8.5px; color: var(--navy);
  }
  .label { color: var(--red); }

  .edge-bar { position: absolute; left: 0; right: 0; bottom: 0; display: flex; gap: 4px; }
  .edge-bar .navy { background: var(--navy); }
  .edge-bar .red { background: var(--red); flex: 1; }
  .letterhead .edge-bar { height: 12px; }
  .letterhead .edge-bar .navy { width: 84%; }
  .business-card .edge-bar { height: 9px; }
  .business-card .edge-bar .navy { width: 79.5%; }

  .holder { position: absolute; left: 0; right: 0; text-align: center; }
  .holder-name { top: 164px; font-size: 18px; color: var(--navy); }
  .holder-title { top: 188px; font-size: 12px; color: var(--red); }
  .card-rule {
    position: absolute; top: 225px; left: 138px; width: 284px;
    height: 2px; background: var(--rule);
  }
  .contact { position: absolute; left: 0; right: 0; top: 252px; text-align: center; font-size: 12.5px; color: var(--navy); line-height: 18px; }
</style>
</head>
<body>
  <section class="sheet letterhead">
    <div class="brand"><span class="brand-square"></span>Brellwick Partners, LLC</div>
    <div class="backdrop-mark"></div>
    <p class="letterhead-footer">408 Larkmoor Lane W · Ashford, PA 19022 &nbsp;|&nbsp; <span class="label">P:</span> 555.214.7730 &nbsp;|&nbsp; <span class="label">W:</span> brellwickpartners.com</p>
    <div class="edge-bar"><span class="navy"></span><span class="red"></span></div>
  </section>

  <section class="sheet business-card">
    <div class="brand"><span class="brand-square"></span>Brellwick Partners, LLC</div>
    <p class="holder holder-name">DANIEL HARTSELL, CFP<sup>®</sup>, MBA</p>
    <p class="holder holder-title">FOUNDER &amp; MANAGING DIRECTOR</p>
    <div class="card-rule"></div>
    <div class="contact">
      <p>408 Larkmoor Lane W · Ashford, PA 19022</p>
      <p><span class="label">P:</span> 555.214.7730 &nbsp;|&nbsp; <span class="label">C:</span> 555.908.4416</p>
      <p><span class="label">E:</span> daniel@brellwickpartners.com &nbsp;|&nbsp; <span class="label">W:</span> brellwickpartners.com</p>
    </div>
    <div class="edge-bar"><span class="navy"></span><span class="red"></span></div>
  </section>
</body>
</html>
```